BrindleStaffing Business Card Design

We are a staffing company finding positions for dedicated nurses and physicians.

Target Market(s)

Business Professionals

Industry/Entity Type

Staffing

Contact Information for Business Card

Gordon Pratley
Chairman
417 39th Avenue South
SAINT PETERSBURG FL 33712
813-555-4172 Mobile
813-555-8036 Fax
gpratley@brindlestaffing.com
www.brindlestaffing.com

Font styles to use
Sans Serif

Colors
fbee3e
f04a50
f37122

Requirements
Must have
• Logo Attached, see colors below. We'd like to see Yellow, Orange and Red.

```html
<!DOCTYPE html>
<html lang="en">
<head>
<meta charset="utf-8">
<title>BrindleStaffing Business Card</title>
<link rel="stylesheet" href="https://fonts.googleapis.com/css2?family=Nunito:wght@700&family=Lato:wght@400;700&display=swap">
<style>
  :root {
    --yellow: #fbee3e;
    --orange: #f37122;
    --red: #f04a50;
    --ink: #222222;
    --muted: #666666;
    --paper: #ffffff;
    --backdrop: #5a5a5a;
  }
  * { margin: 0; padding: 0; box-sizing: border-box; }
  html, body { width: 1200px; height: 802px; overflow: hidden; }
  body { background: var(--backdrop); position: relative; }

  .card {
    position: absolute;
    top: 274px;
    width: 443px;
    height: 265px;
    box-shadow: 2px 3px 6px rgba(0,0,0,0.45);
    overflow: hidden;
  }
  .card--front { left: 136px; background: var(--paper); }
  .card--back {
    left: 624px;
    background: linear-gradient(to bottom, var(--yellow) 0%, var(--orange) 48%, var(--red) 100%);
  }

  .brand {
    position: absolute;
    display: flex;
    align-items: center;
    gap: 6px;
    font-family: "Nunito", sans-serif;
    font-weight: 700;
    white-space: nowrap;
  }
  .brand__dot { border-radius: 50%; display: block; }
  .card--front .brand { left: 24px; top: 46px; font-size: 24px; color: var(--orange); }
  .card--front .brand__dot { width: 8px; height: 8px; background: var(--red); }
  .card--back .brand {
    left: 0; right: 0; top: 114px; justify-content: center;
    font-size: 31px; color: #ffffff;
  }
  .card--back .brand__dot { width: 10px; height: 10px; background: #ffffff; }

  .person {
    position: absolute;
    right: 25px;
    top: 48px;
    text-align: right;
  }
  .person__name {
    font-family: "Nunito", sans-serif;
    font-weight: 700;
    font-size: 18px;
    line-height: 22px;
  }
  .person__first { color: var(--orange); }
  .person__last { color: var(--red); }
  .person__title {
    font-family: "Lato", sans-serif;
    font-size: 11.5px;
    line-height: 15px;
    color: var(--muted);
    letter-spacing: 0.5px;
  }

  .contact-list {
    position: absolute;
    left: 24px;
    top: 176px;
    list-style: none;
    font-family: "Lato", sans-serif;
    font-size: 12.5px;
    color: var(--ink);
    line-height: 16px;
  }
  .contact-list li { display: flex; align-items: center; gap: 4px; white-space: nowrap; }
  .contact-list svg { width: 11px; height: 11px; flex: none; }
  .contact-list__label { color: var(--muted); font-size: 10.5px; margin-left: 2px; }

  .address {
    position: absolute;
    right: 25px;
    top: 208px;
    text-align: right;
    font-family: "Lato", sans-serif;
    font-size: 12.5px;
    line-height: 16px;
    color: var(--ink);
    font-style: normal;
  }

  .accent {
    position: absolute;
    width: 4px;
    border-radius: 2px;
    background: linear-gradient(to bottom, var(--yellow), var(--orange), var(--red));
  }
  .accent--left { left: 6px; top: 178px; height: 62px; }
  .accent--right { right: 6px; top: 194px; height: 46px; background: linear-gradient(to bottom, var(--red), var(--orange), var(--yellow)); }

  .stripe { position: absolute; bottom: 0; height: 8px; width: 50.5%; }
  .stripe--orange { left: 0; background: var(--orange); }
  .stripe--red { right: 0; background: var(--red); }
</style>
</head>
<body>
  <section class="card card--front">
    <div class="brand"><span>BrindleStaffing</span><span class="brand__dot"></span></div>
    <div class="person">
      <div class="person__name"><span class="person__first">Gordon</span> <span class="person__last">Pratley</span></div>
      <div class="person__title">Chairman</div>
    </div>

    <span class="accent accent--left"></span>
    <ul class="contact-list">
      <li>
        <svg viewBox="0 0 12 12" aria-hidden="true"><path fill="#f37122" d="M1 4c0-2 2-3 5-3s5 1 5 3l-2 1-1-1.5H4L3 5 1 4zm2 1h6l1 6H2l1-6zm3 1.5a1.5 1.5 0 100 3 1.5 1.5 0 000-3z"/></svg>
        813-555-4172 <span class="contact-list__label">Mobile</span>
      </li>
      <li>
        <svg viewBox="0 0 12 12" aria-hidden="true"><rect x="3" y="0.5" width="6" height="3.5" fill="#f37122"/><rect x="0.5" y="4" width="11" height="5" rx="1" fill="#f37122"/><rect x="3" y="7.5" width="6" height="4" fill="#f37122" stroke="#fff" stroke-width="0.8"/></svg>
        813-555-8036 <span class="contact-list__label">Fax</span>
      </li>
      <li>
        <svg viewBox="0 0 12 12" aria-hidden="true"><rect x="0.5" y="2" width="11" height="8" fill="#f37122"/><path d="M0.5 2.5 6 7l5.5-4.5" stroke="#fff" stroke-width="1" fill="none"/></svg>
        gpratley@brindlestaffing.com
      </li>
      <li>
        <svg viewBox="0 0 12 12" aria-hidden="true"><circle cx="6" cy="6" r="5.5" fill="#f37122"/><path d="M0.5 6h11M6 0.5c-2.5 3-2.5 8 0 11M6 0.5c2.5 3 2.5 8 0 11" stroke="#fff" stroke-width="0.8" fill="none"/></svg>
        www.brindlestaffing.com
      </li>
    </ul>

    <address class="address">
      417 39th Avenue South<br>
      SAINT PETERSBURG FL 33712
    </address>
    <span class="accent accent--right"></span>

    <span class="stripe stripe--orange"></span>
    <span class="stripe stripe--red"></span>
  </section>

  <section class="card card--back">
    <div class="brand"><span>BrindleStaffing</span><span class="brand__dot"></span></div>
  </section>
</body>
</html>
```